BRISKLY sparkling water needs new artwork! Based in Southern California

"Briskly" is a new sparkling water company based in Southern California that offers refreshing flavors (lime, cherry, & mango) with B vitamins and antioxidants.

We would like to see packaging designs for standard 12oz cans for each of the three flavors.
Our initial preference is to have individual artwork for each flavor.

Attached are examples of competitors' designs.
Updates

We are extending the deadline for the Thanksgiving Holiday. Thank you all for your contributions.

```html
<!DOCTYPE html>
<html lang="en">
<head>
<meta charset="utf-8">
<title>Briskly Sparkling Water – Can Labels</title>
<link rel="stylesheet" href="https://fonts.googleapis.com/css2?family=Antonio:wght@600&family=Montserrat:wght@400;500;600&display=swap">
<style>
  :root{
    --page:#ffffff;
    --lime-pale:#fefee0;
    --lime-yellow:#fcfc9c;
    --lime-green:#1f6b2a;
    --lime-soft:#5a9a46;
    --lime-fruit:#c2e04a;
    --leaf:#5e9f52;
    --cherry:#8b1a22;
    --cherry-tint:#f6e4e6;
    --mango-red:#b9320e;
    --mango-orange:#e9763a;
    --mango-peach:#f9b46b;
    --mango-yellow:#fbd12c;
    --white:#ffffff;
  }
  *{box-sizing:border-box;margin:0;padding:0}
  html,body{width:1200px;height:1000px;overflow:hidden;background:var(--page)}
  body{position:relative;font-family:"Montserrat",sans-serif}
  .label{position:absolute;overflow:hidden}
  .label--lime{left:258px;top:42px;width:614px;height:276px;background:var(--lime-pale)}
  .label--cherry{left:251px;top:348px;width:627px;height:282px;background:var(--white)}
  .label--mango{left:249px;top:659px;width:631px;height:284px}
  .label__art{position:absolute;inset:0;width:100%;height:100%}
  .placeholder{position:absolute}
  .brand{position:absolute;font-family:"Antonio",sans-serif;font-weight:600;font-size:66px;line-height:60px;letter-spacing:1px;text-align:left}
  .flavor{position:absolute;width:200px;text-align:center;font-weight:500;letter-spacing:1px;line-height:1}
  .details{position:absolute;width:260px;text-align:center}
  .details__type{font-size:11px;font-weight:400;letter-spacing:.3px;line-height:13px}
  .details__claim{font-size:7.5px;font-weight:600;margin-top:2px;line-height:9px}
  .details__volume{font-size:6px;font-weight:400;margin-top:4px;line-height:7px}
  .side-text{position:absolute;font-size:4.5px;line-height:6px;writing-mode:vertical-rl;transform:rotate(180deg);width:8px;height:70px;white-space:nowrap}
  .recycle{position:absolute;width:10px;height:10px}
  .label--lime .brand,.label--lime .flavor,.label--lime .side-text{color:var(--lime-green)}
  .label--lime .details{color:var(--lime-soft)}
  .label--cherry .brand,.label--cherry .side-text{color:var(--cherry)}
  .label--cherry .flavor,.label--cherry .details{color:var(--white)}
  .label--mango .brand,.label--mango .flavor,.label--mango .details,.label--mango .side-text{color:var(--white)}
</style>
</head>
<body>

<section class="label label--lime">
  <svg class="label__art" viewBox="0 0 614 276" aria-hidden="true">
    <path d="M0 240 C90 200 160 190 220 205 C300 225 380 190 440 160 C510 125 560 120 614 130 L614 276 L0 276 Z" fill="var(--lime-yellow)"/>
    <path d="M0 258 C120 240 240 232 360 228 C460 224 540 222 614 220" fill="none" stroke="var(--white)" stroke-width="2"/>
    <path d="M150 276 C190 200 300 210 380 170 C450 140 560 130 614 150" fill="none" stroke="var(--white)" stroke-width="1.5"/>
    <path d="M230 0 C300 30 420 40 500 20 C550 8 590 6 614 10" fill="none" stroke="var(--white)" stroke-width="2"/>
  </svg>
  <div class="placeholder" role="img" aria-label="Lime slice illustration" style="left:208px;top:40px;width:220px;height:130px;background:var(--lime-fruit)"></div>
  <div class="placeholder" role="img" aria-label="Lime wedge illustration" style="left:0;top:0;width:62px;height:58px;background:var(--lime-fruit)"></div>
  <div class="placeholder" role="img" aria-label="Lime wedge illustration" style="left:478px;top:240px;width:114px;height:36px;background:var(--lime-fruit)"></div>
  <div class="placeholder" role="img" aria-label="Leaf illustration" style="left:557px;top:63px;width:57px;height:80px;background:var(--leaf)"></div>
  <div class="placeholder" role="img" aria-label="Leaf illustration" style="left:0;top:122px;width:16px;height:38px;background:var(--leaf)"></div>
  <p class="side-text" style="left:24px;top:123px">Briskly Beverage Co, CA</p>
  <svg class="recycle" style="left:25px;top:248px" viewBox="0 0 10 10" aria-hidden="true"><path d="M5 1 L9 8 H1 Z" fill="none" stroke="var(--lime-green)" stroke-width="1.2"/></svg>
  <h1 class="brand" style="left:283px;top:20px">BR<br>IS<br>KLY</h1>
  <p class="flavor" style="left:222px;top:202px;font-size:20px;font-weight:400;letter-spacing:2px">LIME</p>
  <div class="details" style="left:190px;top:232px">
    <p class="details__type">SPARKLING WATER</p>
    <p class="details__claim">Made with B vitamins and antioxidants</p>
    <p class="details__volume">12 FL OZ (355ML)</p>
  </div>
</section>

<section class="label label--cherry">
  <div class="placeholder" role="img" aria-label="Line illustration of a cherry with stem" style="left:183px;top:0;width:200px;height:195px;background:linear-gradient(135deg,var(--cherry-tint),var(--white))"></div>
  <svg class="label__art" viewBox="0 0 627 282" aria-hidden="true">
    <path d="M0 200 C80 190 160 212 240 202 C320 192 400 190 470 204 C540 216 590 200 627 195 L627 282 L0 282 Z" fill="var(--cherry)"/>
    <path d="M0 208 C90 196 170 222 250 212 C330 202 410 200 480 214 C550 226 600 214 627 222" fill="none" stroke="var(--white)" stroke-width="1.5"/>
  </svg>
  <p class="side-text" style="left:16px;top:130px">Briskly Beverage Co, CA</p>
  <svg class="recycle" style="left:25px;top:247px" viewBox="0 0 10 10" aria-hidden="true"><path d="M5 1 L9 8 H1 Z" fill="none" stroke="var(--white)" stroke-width="1.2"/></svg>
  <h1 class="brand" style="left:271px;top:14px">BR<br>IS<br>KLY</h1>
  <p class="flavor" style="left:209px;top:198px;font-size:15px;font-weight:400">CHERRY</p>
  <div class="details" style="left:181px;top:230px">
    <p class="details__type">SPARKLING WATER</p>
    <p class="details__claim">Made with B vitamins and antioxidants</p>
    <p class="details__volume">12 FL OZ (355ML)</p>
  </div>
</section>

<section class="label label--mango">
  <div class="placeholder" role="img" aria-label="Abstract mango-toned paint splash illustration" style="inset:0;background:linear-gradient(90deg,var(--mango-orange) 0%,var(--mango-red) 12%,var(--mango-red) 42%,var(--mango-orange) 55%,var(--mango-peach) 72%,var(--mango-yellow) 100%)"></div>
  <p class="side-text" style="left:18px;top:136px">Briskly Beverage Co, CA</p>
  <svg class="recycle" style="left:24px;top:270px" viewBox="0 0 10 10" aria-hidden="true"><path d="M5 1 L9 8 H1 Z" fill="none" stroke="var(--white)" stroke-width="1.2"/></svg>
  <h1 class="brand" style="left:290px;top:16px">BR<br>IS<br>KLY</h1>
  <p class="flavor" style="left:229px;top:201px;font-size:15px;font-weight:400">MANGO</p>
  <div class="details" style="left:199px;top:234px">
    <p class="details__type">SPARKLING WATER</p>
    <p class="details__claim">Made with B vitamins and antioxidants</p>
    <p class="details__volume">12 FL OZ (355ML)</p>
  </div>
</section>

</body>
</html>
```